Basic business card

use my newly created logo - and the phrases (Lower Cost of Test & Accelarated New Product Introduction) - and my new email domain / ID - use at conferences / tradeshows

Industry/Entity Type

semiconductor

Contact Information for Business Card

Daniel K Forde, Owner, communicate via Logo - Lower COT - Cost of Test, Accelerated NPI - New Product Introduction, phone +1 555 613 0946, Chandler, Arizona, USA, daniel.forde@qal-vub.com

Font styles to use
Sans Serif

Requirements
Nice to have
• re-use my logo created via Pixel Harbor last August (#7315926)

```html
<!DOCTYPE html>
<html lang="en">
<head>
<meta charset="utf-8">
<title>QAL-VUB Business Card</title>
<link href="https://fonts.googleapis.com/css2?family=Open+Sans:wght@400;600;700&display=swap" rel="stylesheet">
<style>
  :root {
    --page: #222222;
    --card: #1e1e22;
    --edge: #7dc242;
    --green: #7dc242;
    --orange: #f7941d;
    --white: #ffffff;
    --slate: #4b5674;
    --emboss: #141417;
  }
  * { box-sizing: border-box; margin: 0; padding: 0; }
  html, body { width: 1200px; height: 780px; overflow: hidden; background: var(--page); }
  body { font-family: "Open Sans", Arial, sans-serif; position: relative; }

  .card {
    position: absolute;
    left: 290px;
    width: 620px;
    height: 354px;
    background: var(--card);
    border-radius: 22px;
    border: 3px solid var(--edge);
    overflow: hidden;
  }
  .card--front { top: 28px; }
  .card--back { top: 398px; }

  /* Front: blind-embossed company name */
  .front-brand {
    position: absolute; left: 0; right: 0; top: 0; bottom: 0;
    display: flex; align-items: center; justify-content: center; gap: 16px;
  }
  .front-brand__mark { width: 34px; height: 34px; background: var(--emboss); }
  .front-brand__name {
    font-size: 78px; font-weight: 600; letter-spacing: 2px; color: var(--emboss);
  }

  /* Back: details */
  .brand {
    position: absolute; left: 34px; top: 26px;
    display: flex; align-items: center; gap: 10px;
  }
  .brand__mark { width: 22px; height: 22px; background: var(--slate); }
  .brand__name { font-size: 40px; font-weight: 600; letter-spacing: 1px; color: var(--slate); }

  .person {
    position: absolute; right: 38px; top: 40px; text-align: right;
  }
  .person__name { font-size: 30px; font-weight: 700; line-height: 1.1; }
  .person__first { color: var(--green); }
  .person__last { color: var(--orange); }
  .person__title { font-size: 16px; color: var(--white); margin-top: 4px; }
  .accent-bar {
    position: absolute; right: 0; top: 34px; width: 20px; height: 64px; background: var(--green);
  }

  .address {
    position: absolute; left: 130px; top: 180px;
    font-size: 15px; line-height: 1.45; color: var(--white);
  }
  .contact {
    position: absolute; left: 130px; top: 250px; list-style: none;
    font-size: 15px; line-height: 1.55; color: var(--white);
  }
  .contact li { display: flex; align-items: center; gap: 10px; }
  .contact svg { width: 15px; height: 15px; flex: none; }
</style>
</head>
<body>
  <section class="card card--front" aria-label="Card front">
    <div class="front-brand">
      <span class="front-brand__mark"></span>
      <span class="front-brand__name">QAL-VUB</span>
    </div>
  </section>

  <section class="card card--back" aria-label="Card back">
    <div class="brand">
      <span class="brand__mark"></span>
      <span class="brand__name">QAL-VUB</span>
    </div>

    <div class="accent-bar"></div>
    <div class="person">
      <p class="person__name"><span class="person__first">Mira</span> <span class="person__last">Kovalenko</span></p>
      <p class="person__title">Managing Director</p>
    </div>

    <address class="address" style="font-style:normal">
      418 Harbor Crest Ave. Suite 120<br>
      Millbrook, TX 75013
    </address>

    <ul class="contact">
      <li>
        <svg viewBox="0 0 16 16" aria-hidden="true"><path fill="#7dc242" d="M3.5 1.5l2.5 0 1 3.5-1.8 1.2a8 8 0 0 0 4.6 4.6L11 9l3.5 1v2.5c0 1-1 2-2 2A11 11 0 0 1 1.5 3.5c0-1 1-2 2-2z"/></svg>
        (555) 274-0183
      </li>
      <li>
        <svg viewBox="0 0 16 16" aria-hidden="true"><rect x="1" y="3.5" width="14" height="9" fill="none" stroke="#7dc242" stroke-width="1.6"/><path d="M1.5 4l6.5 5 6.5-5" fill="none" stroke="#7dc242" stroke-width="1.6"/></svg>
        info@qal-vub.com
      </li>
      <li>
        <svg viewBox="0 0 16 16" aria-hidden="true"><circle cx="8" cy="8" r="6.5" fill="none" stroke="#7dc242" stroke-width="1.5"/><ellipse cx="8" cy="8" rx="2.8" ry="6.5" fill="none" stroke="#7dc242" stroke-width="1.2"/><path d="M1.5 8h13" stroke="#7dc242" stroke-width="1.2"/></svg>
        www.qal-vub.com
      </li>
    </ul>
  </section>
</body>
</html>
```